Landscape design build company door flyer

I would like this flyer to convey a high-level of professionalism for a company that is excellent with communication with their clients as well as a company that does incredible installations

Went on vacation/holiday

```html
<!DOCTYPE html>
<html lang="en">
<head>
<meta charset="UTF-8">
<title>Cedarline Builders – Outdoor Living Spaces Flyer</title>
<link href="https://fonts.googleapis.com/css2?family=Poppins:wght@400;500;600;700;800&display=swap" rel="stylesheet">
<style>
  :root {
    --navy: #0b2a3e;
    --orange: #f56a08;
    --gold: #f5a700;
    --paper: #f1f1f1;
    --stage: #e4e4e4;
    --ink: #1b1b1b;
    --white: #ffffff;
  }
  * { box-sizing: border-box; margin: 0; padding: 0; }
  html, body {
    width: 1200px; height: 1029px; overflow: hidden;
    background: var(--stage);
    font-family: "Poppins", sans-serif;
  }
  .flyer {
    position: absolute; left: 200px; top: 0;
    width: 800px; height: 1029px;
    background: var(--paper); overflow: hidden;
  }
  .brand {
    position: absolute; left: 0; top: 0; width: 353px; height: 164px;
    display: flex; flex-direction: column; align-items: center; justify-content: center;
    gap: 4px; padding-top: 18px;
  }
  .brand-dot { width: 44px; height: 44px; border-radius: 50%; background: var(--orange); margin-bottom: 8px; }
  .brand-name { font-weight: 600; font-size: 17px; color: var(--orange); letter-spacing: 0.5px; }
  .brand-tagline { font-weight: 500; font-size: 8.5px; color: var(--navy); letter-spacing: 0.3px; }

  .hero-photo {
    position: absolute; left: 353px; top: 0; width: 447px; height: 484px;
    background: linear-gradient(180deg, #8fb3d9 0%, #b9c7d2 30%, #9a6a3e 55%, #7f7f85 75%, #5f9a3a 100%);
  }
  .hero-panel { position: absolute; left: 0; top: 0; width: 800px; height: 484px; }
  .headline {
    position: absolute; left: 37px; top: 205px;
    font-weight: 700; font-size: 48px; line-height: 58px; letter-spacing: -0.5px;
    color: var(--white); text-transform: uppercase;
  }
  .headline .accent { color: var(--orange); }

  .section-title {
    position: absolute; font-weight: 800; font-size: 23px; color: var(--navy); letter-spacing: -0.3px;
  }
  .section-title::after {
    content: ""; position: absolute; left: 0; top: 34px; width: 66px; height: 3px;
    border-radius: 2px; background: linear-gradient(90deg, var(--gold), #f7c24a 70%, transparent);
  }
  .about-title { left: 37px; top: 500px; }
  .about-text {
    position: absolute; left: 37px; top: 553px; width: 338px;
    font-size: 12.2px; line-height: 15.2px; color: var(--ink); text-align: justify; hyphens: auto;
  }
  .services-title { left: 441px; top: 500px; }
  .service-list { position: absolute; left: 441px; top: 555px; list-style: none; }
  .service-list li {
    display: flex; align-items: center; gap: 16px;
    font-weight: 500; font-size: 14.5px; line-height: 21.7px; color: var(--navy);
  }
  .service-list svg { width: 13px; height: 13px; flex: none; }

  .works-rule {
    position: absolute; left: 30px; top: 740px; width: 743px; height: 1.5px;
    background: linear-gradient(90deg, transparent, var(--gold) 20%, var(--gold) 80%, transparent);
  }
  .works-title {
    position: absolute; left: 283px; top: 722px; width: 227px; height: 30px;
    background: var(--orange); color: var(--white);
    font-weight: 700; font-size: 19px; line-height: 30px; text-align: center;
  }
  .work-photo { position: absolute; top: 767px; width: 216px; height: 117px; }
  .work-1 { left: 41px; background: linear-gradient(180deg, #5d6a6e 0%, #b08070 30%, #9d6d60 100%); }
  .work-2 { left: 293px; background: linear-gradient(180deg, #6f8a6a 0%, #5e6a72 30%, #a3a7ab 60%, #8a8f93 100%); }
  .work-3 { left: 539px; background: linear-gradient(180deg, #4e5a48 0%, #a4552d 45%, #7eb04a 75%, #6aa23c 100%); }

  .footer { position: absolute; left: 0; top: 927px; width: 800px; height: 102px; }
  .phone-icon { position: absolute; left: 38px; top: 952px; width: 52px; height: 52px; background: var(--orange);
    display: flex; align-items: center; justify-content: center; }
  .phone-icon svg { width: 30px; height: 30px; }
  .phone-number {
    position: absolute; left: 102px; top: 950px;
    font-weight: 700; font-size: 44px; line-height: 56px; letter-spacing: -1px; color: var(--white);
  }
  .contact { position: absolute; left: 532px; list-style: none; }
  .contact li { display: flex; align-items: center; gap: 14px; color: var(--white); font-size: 14.5px; line-height: 26px; }
  .contact svg { width: 16px; height: 16px; flex: none; }
</style>
</head>
<body>
<main class="flyer">
  <div class="brand">
    <span class="brand-dot"></span>
    <span class="brand-name">CEDARLINE BUILDERS</span>
    <span class="brand-tagline">OUTDOOR LIVING SPACES</span>
  </div>

  <div class="hero-photo" role="img" aria-label="Photo of a cedar pavilion over a stone outdoor kitchen with paver patio, fence and lawn"></div>

  <svg class="hero-panel" viewBox="0 0 800 484" aria-hidden="true">
    <polygon points="0,164 376,164 534,484 0,484" fill="var(--navy)"/>
  </svg>

  <h1 class="headline">Let’s create<br>your dream<br><span class="accent">Outdoor<br>living space!</span></h1>

  <h2 class="section-title about-title">ABOUT US</h2>
  <p class="about-text">Discover the endless possibilities for your outdoor space with The Cedarline Builders Team. Our team of skilled artisans is dedicated to turning your outdoor space into a breathtaking oasis that you’ll love coming home to. Whether it’s a cozy patio for intimate gatherings, a sprawling deck to host memorable parties, or a custom paver driveway that adds instant curb appeal, our high-quality craftsmanship ensures stunning results that exceed your expectations.</p>

  <h2 class="section-title services-title">OUR SERVICES</h2>
  <ul class="service-list">
    <li><svg viewBox="0 0 14 14"><circle cx="7" cy="7" r="7" fill="var(--orange)"/><path d="M3.8 7.2l2.2 2.2 4.3-4.5" stroke="#fff" stroke-width="1.8" fill="none"/></svg>Paver Patios</li>
    <li><svg viewBox="0 0 14 14"><circle cx="7" cy="7" r="7" fill="var(--orange)"/><path d="M3.8 7.2l2.2 2.2 4.3-4.5" stroke="#fff" stroke-width="1.8" fill="none"/></svg>Paver Driveways</li>
    <li><svg viewBox="0 0 14 14"><circle cx="7" cy="7" r="7" fill="var(--orange)"/><path d="M3.8 7.2l2.2 2.2 4.3-4.5" stroke="#fff" stroke-width="1.8" fill="none"/></svg>Retaining Walls</li>
    <li><svg viewBox="0 0 14 14"><circle cx="7" cy="7" r="7" fill="var(--orange)"/><path d="M3.8 7.2l2.2 2.2 4.3-4.5" stroke="#fff" stroke-width="1.8" fill="none"/></svg>Decks &amp; Railings</li>
    <li><svg viewBox="0 0 14 14"><circle cx="7" cy="7" r="7" fill="var(--orange)"/><path d="M3.8 7.2l2.2 2.2 4.3-4.5" stroke="#fff" stroke-width="1.8" fill="none"/></svg>Pools</li>
    <li><svg viewBox="0 0 14 14"><circle cx="7" cy="7" r="7" fill="var(--orange)"/><path d="M3.8 7.2l2.2 2.2 4.3-4.5" stroke="#fff" stroke-width="1.8" fill="none"/></svg>Outdoor Lighting</li>
    <li><svg viewBox="0 0 14 14"><circle cx="7" cy="7" r="7" fill="var(--orange)"/><path d="M3.8 7.2l2.2 2.2 4.3-4.5" stroke="#fff" stroke-width="1.8" fill="none"/></svg>Firepits &amp; Fireplaces</li>
  </ul>

  <div class="works-rule"></div>
  <h2 class="works-title">OUR WORKS</h2>
  <div class="work-photo work-1" role="img" aria-label="Photo of composite deck stairs with step lights beside a hot tub"></div>
  <div class="work-photo work-2" role="img" aria-label="Photo of a grey composite deck with black metal railing"></div>
  <div class="work-photo work-3" role="img" aria-label="Photo of a wraparound stained wood deck on a house surrounded by lawn and trees"></div>

  <svg class="footer" viewBox="0 0 800 102" aria-hidden="true">
    <polygon points="0,7 486,7 444,102 0,102" fill="var(--navy)"/>
    <polygon points="488,0 800,0 800,102 444,102" fill="var(--orange)"/>
  </svg>
  <div class="phone-icon">
    <svg viewBox="0 0 24 24"><path fill="#fff" d="M6.6 10.8c1.4 2.8 3.8 5.1 6.6 6.6l2.2-2.2c.3-.3.7-.4 1-.2 1.1.4 2.3.6 3.6.6.6 0 1 .4 1 1V20c0 .6-.4 1-1 1C10.6 21 3 13.4 3 4c0-.6.4-1 1-1h3.5c.6 0 1 .4 1 1 0 1.3.2 2.5.6 3.6.1.3 0 .7-.2 1L6.6 10.8z"/></svg>
  </div>
  <p class="phone-number">206-555-0148</p>
  <ul class="contact" style="top:945px;">
    <li><svg viewBox="0 0 16 16"><rect x="1" y="3" width="14" height="10" fill="#fff"/><path d="M1 3l7 5.5L15 3" stroke="var(--orange)" stroke-width="1.5" fill="none"/></svg>hello@cedarlinebuilders.com</li>
    <li><svg viewBox="0 0 16 16" fill="none" stroke="#fff" stroke-width="1.2"><circle cx="8" cy="8" r="6.5"/><ellipse cx="8" cy="8" rx="3" ry="6.5"/><path d="M1.5 8h13M2.5 5h11M2.5 11h11"/></svg>www.cedarlinebuilders.com</li>
  </ul>
</main>
</body>
</html>
```